KTWG application splash screen

We need a 1024x768 image for use as an application splash screen.
The image will be displayed full screen on an 10 inch industrial PC 1024x768 screen while our application is launching. The image should convey that the application is "Waiting for connection to Wi-Fi access point..." and include a graphic of the industrial PC connected to the access point via an Ethernet cable. A list of troubleshooting steps should be included at the bottom of the image. The troubleshooting steps should not be the main focus of the image and should be shown in a smaller font (but still readable at 1024x768 displayed on a 10 inch screen).
I will include a mock up of the general idea of what we are looking for as well as image files for the industrial PC, a screenshot of our application to show on the PC's screen and the AP.
For general look and feel and a sense of corporate branding please review our website https://marrowgatesoilworks.example/. The splash screen should reflect corporate branding.
Target Market(s)
Users of our application
Industry/Entity Type
Agriculture
Look and feel

```html
<!DOCTYPE html>
<html lang="en">
<head>
<meta charset="utf-8">
<title>KTWG – Waiting for Wi-Fi access point</title>
<link href="https://fonts.googleapis.com/css2?family=Poppins:wght@300;400;500;600;700&display=swap" rel="stylesheet">
<style>
  :root {
    --backdrop: #000000;
    --panel: #73bd8a;
    --card: #ffffff;
    --brand-green: #3dba63;
    --device-dark: #2b2b2b;
    --device-screen: #dfe7e2;
    --ap-white: #eef0ef;
    --tile-dark: #000000;
  }
  * { margin: 0; padding: 0; box-sizing: border-box; }
  html, body {
    width: 1200px; height: 1200px; overflow: hidden;
    background: var(--backdrop);
    font-family: "Poppins", sans-serif;
  }
  .canvas { position: relative; width: 1200px; height: 1200px; }
  .splash {
    position: absolute; left: 110px; top: 233px;
    width: 978px; height: 733px;
    background: var(--panel);
  }
  .headline-card {
    position: absolute; left: 283px; top: 0;
    width: 413px; height: 163px;
    background: var(--card);
    border-radius: 0 0 22px 22px;
    text-align: center;
    padding-top: 42px;
  }
  .headline {
    color: var(--brand-green);
    font-weight: 700; font-size: 31px; line-height: 34px;
    letter-spacing: 1.5px;
  }
  .device-card {
    position: absolute; top: 270px;
    width: 254px; height: 205px;
    background: var(--card);
    border-radius: 19px;
    text-align: center;
  }
  .device-card.computer { left: 65px; }
  .device-card.access-point { left: 659px; }
  .device-title {
    position: absolute; left: 0; right: 0; top: 135px;
    color: var(--brand-green);
    font-weight: 700; font-size: 19.6px; letter-spacing: 1.5px;
  }
  .device-subtitle {
    position: absolute; left: 0; right: 0; top: 162px;
    color: var(--brand-green);
    font-weight: 400; font-size: 13.2px; letter-spacing: 1.1px;
  }
  .computer-graphic {
    position: absolute; left: 106px; top: 245px;
    width: 173px; height: 138px;
    border-radius: 8px;
    background: linear-gradient(160deg, #3a3a3a, var(--device-dark));
    border: 6px solid var(--device-dark);
  }
  .computer-graphic::after {
    content: ""; position: absolute; left: 10px; top: 8px; right: 10px; bottom: 18px;
    background: linear-gradient(180deg, var(--device-screen), #c9ddd0);
    border-radius: 2px;
  }
  .ap-graphic {
    position: absolute; left: 775px; top: 243px;
    width: 22px; height: 143px;
    border-radius: 6px;
    background: linear-gradient(90deg, #d9dcdb, var(--ap-white), #d4d7d6);
  }
  .ethernet-link {
    position: absolute; left: 336px; top: 375px; width: 307px; height: 6px;
  }
  .ethernet-label {
    position: absolute; left: 336px; top: 388px; width: 307px;
    text-align: center; color: var(--card);
    font-weight: 700; font-size: 19.2px; letter-spacing: 1.5px;
  }
  .troubleshooting {
    position: absolute; left: 276px; top: 579px;
    width: 426px; height: 154px;
    background: var(--card);
    border-radius: 19px 19px 0 0;
    color: var(--brand-green);
  }
  .troubleshooting h2 {
    text-align: center; margin-top: 11px;
    font-weight: 700; font-size: 14px; letter-spacing: 1.2px;
  }
  .steps { list-style: none; margin: 3px 0 0 28px; font-size: 9.7px; line-height: 11.5px; font-weight: 400; }
  .steps li { padding-left: 7px; text-indent: -7px; }
  .steps li::before { content: "• "; }
  .steps .sub { margin-left: 13px; padding-left: 7px; }
  .brand-tile {
    position: absolute; left: 856px; top: 615px;
    width: 89px; height: 89px;
    background: var(--tile-dark);
    border: 3px solid var(--card);
    border-radius: 20px;
    display: flex; align-items: center; justify-content: center;
  }
  .brand-name { color: var(--card); font-weight: 700; font-size: 22px; letter-spacing: 1px; }
</style>
</head>
<body>
<div class="canvas">
  <section class="splash">
    <div class="headline-card">
      <h1 class="headline">Waiting for<br>connection to Wi-Fi<br>access point...</h1>
    </div>

    <div class="device-card computer">
      <div class="device-title">TRACTOR CAB</div>
      <div class="device-subtitle">COMPUTER</div>
    </div>
    <div class="computer-graphic" role="img" aria-label="Industrial tractor cab computer showing the KTWG application"></div>

    <svg class="ethernet-link" viewBox="0 0 307 6" aria-hidden="true">
      <line x1="3" y1="3" x2="304" y2="3" stroke="#ffffff" stroke-width="5" stroke-linecap="round" stroke-dasharray="0 11.6"/>
    </svg>
    <div class="ethernet-label">ETHERNET CABLE</div>

    <div class="device-card access-point">
      <div class="device-title">WI-FI ACCESS POINT</div>
      <div class="device-subtitle">NETHAVEN RV30-OUTDOOR</div>
    </div>
    <div class="ap-graphic" role="img" aria-label="Outdoor Wi-Fi access point with two antennas"></div>

    <div class="troubleshooting">
      <h2>TROUBLESHOOTING STEPS:</h2>
      <ul class="steps">
        <li>This screen should only be visible for a short time on boot.</li>
        <li>If this screen stays visible for more than a minute:</li>
        <li class="sub">Verify that the Wi-Fi Access Point (AP) powers up when this system does (indicated by a green light on the side of the AP).</li>
        <li class="sub">Check the Ethernet cable between this system and the AP for damage, and replace it if necessary.</li>
        <li class="sub">Power-cycle this system and wait for it to reboot fully.</li>
        <li class="sub">If the issue persists, contact KTWG support for further assistance.</li>
      </ul>
    </div>

    <div class="brand-tile"><span class="brand-name">KTWG</span></div>
  </section>
</div>
</body>
</html>
```